Torvadex needs a website to buy and sell phones and electronics

We need a website to buy and sell smartphones.
https://www.quicklorratrade.com/
http://www.bramblequayshop.co.uk/
http://tradeyourunit.halvestorndepot.com/
https://www.k9loopbacker.co.uk/
https://www.brolvenmartex.co.uk/we-buy/

I logged into plorna.com and went to their online store template. I iike their template on the camera shop. I like the big letters but with elegance and formality. See link below:
http://www.plorna.com/website-template/view/html/1625?originUrl=http%3A%2F%2Fwww.plorna.com%2Fwebsite%2Ftemplates%2Fhtml%2Fonline-store%2F2&bookName=&galleryDocIndex=0&category=online-store

We know that these websites are too much work but we only need the landing page, without the that big search box. We want the various qavrixes such Qavrixes 4, 5, 6 and 7 and Turnwell Orbit S3, S4, S5 and S6 be listed with corresponding prices in Philippine currency.

We don't have a logo yet.

Notes To Designers: I would like to have a good feel of the site and I hope these sites can give you a feel. - quicklorratrade.com - bramblequayshop.co.uk Note: Please read the brief for updates. Also: i paid for the coded website so I believe it must be a running website. Thank you.

Target Market(s)

Philippines

Industry/Entity Type

Electronics

Coding

Coded - Design and coding required

Number of Pages Required

5+ page

Requirements
Must have
• Must displays phones of Qavrixes and Turnwell (Only the latest models for the last 2-3 years) not old
• Lumtabs and Kordial as well
Nice to have
• Logo - we need logo
• I love the simplicity but elegance of https://www.quicklorratrade.com/

```html
<!DOCTYPE html>
<html lang="en">
<head>
<meta charset="utf-8">
<title>Torvadex – Buy and sell smartphones</title>
<link href="https://fonts.googleapis.com/css2?family=Open+Sans:wght@400;600&family=Oswald:wght@300;400&display=swap" rel="stylesheet">
<style>
:root{
  --blue:#2d7dc1;
  --blue-dark:#1f6aa9;
  --orange:#f0901c;
  --orange-deep:#e07f10;
  --ink:#222;
  --muted:#777;
  --panel:#f1f1f1;
  --line:#d6d6d6;
  --white:#fff;
}
*{margin:0;padding:0;box-sizing:border-box}
html,body{width:792px;height:1200px;overflow:hidden;background:var(--white)}
body{position:relative;font-family:"Open Sans",sans-serif;color:var(--ink);font-weight:400}
.abs{position:absolute}

.topbar{left:0;top:0;width:792px;height:23px;background:var(--blue);color:var(--white);font-size:8.5px}
.topbar .contact{left:60px;top:6px;display:flex;gap:14px}
.topbar .contact span{display:flex;align-items:center;gap:4px}
.topbar .account{left:615px;top:6px}
.topbar .socials{left:683px;top:6px;display:flex;gap:4px}
.topbar .socials i{display:block;width:9px;height:9px;border-radius:2px;background:var(--white)}

.header{left:0;top:23px;width:792px;height:59px;background:var(--white)}
.brand{font-family:"Open Sans",sans-serif;font-weight:600;color:var(--orange);letter-spacing:2px}
.header .brand{left:60px;top:17px;font-size:20px}
.nav{left:299px;top:24px;display:flex;gap:29px;font-size:9.5px;text-transform:uppercase}
.nav a{color:var(--ink);text-decoration:none}
.nav a.active{color:var(--blue)}
.header .search{left:691px;top:23px}
.header .cart{left:713px;top:16px;width:21px;height:22px;background:var(--orange)}

.hero{left:0;top:82px;width:792px;height:344px;background:linear-gradient(110deg,#d9dde3 0%,#c9cdd3 30%,#2b3440 45%,#1d232b 55%,#e8e2da 70%,#f3efe9 100%)}
.hero-title{left:57px;top:304px;font-family:"Oswald",sans-serif;font-weight:400;font-size:37px;color:var(--blue-dark);line-height:1}
.hero-sub{left:57px;top:346px;font-family:"Oswald",sans-serif;font-weight:300;font-size:21px;color:var(--orange);line-height:1}
.slider-btn{top:384px;width:24px;height:24px;border-radius:50%;background:rgba(60,45,30,.8)}

.features{left:0;top:428px;width:792px;height:125px;display:flex;gap:2px}
.feature{flex:1;background:var(--panel);text-align:center;padding-top:24px}
.feature svg{display:block;margin:0 auto 12px}
.feature h3{font-weight:400;font-size:11.5px;letter-spacing:.2px}
.feature p{font-size:8px;color:var(--muted);margin-top:6px}

.section-title{left:0;top:598px;width:792px;text-align:center;font-size:21px;font-weight:400;letter-spacing:.5px}
.products{left:59px;top:648px;display:flex;gap:12px}
.card{width:160px;height:209px;background:var(--white);box-shadow:0 1px 4px rgba(0,0,0,.22);text-align:center;padding-top:13px}
.card .shot{width:64px;height:131px;margin:0 auto;border-radius:9px;background:linear-gradient(180deg,#e7e7e7,#9aa4b3 50%,#d9d9d9)}
.card .shot.dark{background:linear-gradient(180deg,#2a2a33,#5a5470 60%,#2a2a33)}
.card .shot.gold{background:linear-gradient(180deg,#e8e0cc,#9bb8d8 50%,#ddd4bd)}
.card h4{font-weight:400;font-size:9.5px;margin-top:20px}
.card .price{font-size:11.5px;color:var(--blue);margin-top:8px;display:flex;justify-content:center;align-items:center;gap:4px;white-space:nowrap}

.cta{left:0;top:908px;width:792px;height:102px;background:linear-gradient(100deg,var(--orange-deep),var(--orange) 45%,#f3a23a 75%,var(--orange-deep));color:var(--white)}
.cta h2{position:absolute;left:59px;top:30px;font-weight:400;font-size:19px;letter-spacing:.3px}
.cta p{position:absolute;left:59px;top:56px;font-size:14px}
.cta .btn{position:absolute;left:621px;top:32px;width:111px;height:33px;background:#f7f7f7;color:#333;font-size:12px;display:flex;align-items:center;justify-content:center;box-shadow:0 1px 2px rgba(0,0,0,.2)}

.footer .brand{left:57px;top:1082px;font-size:18px}
.col-title{top:1052px;font-size:9.5px;font-weight:400;text-transform:uppercase}
.col-text{font-size:7.2px;color:#555;line-height:14.5px;font-weight:400}
.newsletter{left:429px;top:1103px;display:flex}
.newsletter .field{width:97px;height:20px;border:1px solid #ccc;font-size:7.5px;color:#666;padding:5px 0 0 6px}
.newsletter .submit{width:37px;height:20px;background:var(--blue);color:var(--white);font-size:8px;display:flex;align-items:center;justify-content:center}
.follow{left:626px;top:1081px;display:flex;gap:10px}
.follow i{display:block;width:16px;height:16px;border-radius:3px;background:#555}
.rule{left:57px;top:1160px;width:675px;height:1px;background:var(--line)}
.copyright{left:0;top:1178px;width:792px;text-align:center;font-size:8px;font-weight:400}
</style>
</head>
<body>

<div class="abs topbar">
  <div class="abs contact">
    <span><svg width="8" height="8" viewBox="0 0 10 10"><rect width="10" height="10" rx="2" fill="#fff"/><path d="M3 2.5l1.2 1.2-.7.8c.4.9 1 1.5 1.9 1.9l.8-.7L7.5 7 6.7 8C4.3 7.6 2.4 5.7 2 3.3z" fill="#2d7dc1"/></svg>: +63-2-555-0184</span>
    <span><svg width="9" height="7" viewBox="0 0 10 8"><rect width="10" height="8" rx="1" fill="#fff"/><path d="M0 1l5 3.5L10 1" stroke="#2d7dc1" fill="none"/></svg>: info@torvadexmail.com</span>
  </div>
  <div class="abs account">My Account ▾</div>
  <div class="abs socials"><i></i><i></i><i></i><i></i></div>
</div>

<header class="abs header">
  <div class="abs brand">TORVADEX</div>
  <nav class="abs nav">
    <a class="active" href="#">Home</a><a href="#">Products</a><a href="#">About us</a><a href="#">Supports</a><a href="#">Blog</a><a href="#">Contact</a>
  </nav>
  <svg class="abs search" width="10" height="10" viewBox="0 0 10 10"><circle cx="4" cy="4" r="3" stroke="#222" stroke-width="1.6" fill="none"/><path d="M6.2 6.2L9.3 9.3" stroke="#222" stroke-width="1.8"/></svg>
  <div class="abs cart">
    <svg width="21" height="22" viewBox="0 0 21 22"><path d="M6 7h1.5l1.3 6h5.5l1.2-4.5H8.2" stroke="#fff" stroke-width="1.2" fill="none"/><circle cx="9.5" cy="15" r="1" fill="#fff"/><circle cx="13.5" cy="15" r="1" fill="#fff"/></svg>
  </div>
</header>

<section class="abs hero" role="img" aria-label="Photo of a hand holding a smartphone full of app icons beside a laptop and a cup of coffee"></section>
<div class="abs hero-title">TORVADEX</div>
<div class="abs hero-sub">Buy and sell smartphones</div>
<div class="abs slider-btn" style="left:682px"><svg width="24" height="24" viewBox="0 0 24 24"><path d="M14 7l-5 5 5 5" stroke="#fff" stroke-width="2" fill="none"/></svg></div>
<div class="abs slider-btn" style="left:708px"><svg width="24" height="24" viewBox="0 0 24 24"><path d="M10 7l5 5-5 5" stroke="#fff" stroke-width="2" fill="none"/></svg></div>

<section class="abs features">
  <div class="feature">
    <svg width="34" height="34" viewBox="0 0 34 34"><circle cx="17" cy="17" r="17" fill="var(--blue)"/><path d="M13 25V9h5a4.5 4.5 0 010 9h-5M10 12.5h14M10 15h14" stroke="#fff" stroke-width="2.2" fill="none"/></svg>
    <h3>PRICE GUARANTEE</h3><p>We promise to pay our quoted</p>
  </div>
  <div class="feature">
    <svg width="38" height="34" viewBox="0 0 38 34"><rect x="1" y="3" width="36" height="23" rx="2" fill="var(--blue)"/><rect x="4" y="6" width="30" height="15" fill="#f1f1f1"/><rect x="15" y="26" width="8" height="5" fill="var(--blue)"/><rect x="11" y="31" width="16" height="2" fill="var(--blue)"/></svg>
    <h3>FAST PAYMENT</h3><p>We pay the money directly</p>
  </div>
  <div class="feature">
    <svg width="48" height="34" viewBox="0 0 48 34"><g fill="none" stroke="var(--blue)" stroke-width="2"><rect x="2" y="9" width="12" height="22" rx="2"/><rect x="18" y="2" width="13" height="30" rx="2"/><rect x="35" y="9" width="11" height="22" rx="2"/></g></svg>
    <h3>WE TAKE ALL PHONES</h3><p>We take all kinds of phones</p>
  </div>
</section>

<h2 class="abs section-title">OUR PRODUCTS</h2>
<svg class="abs" style="left:33px;top:735px" width="14" height="26" viewBox="0 0 14 26"><path d="M12 1L2 13l10 12" stroke="#777" fill="none"/></svg>
<svg class="abs" style="left:745px;top:735px" width="14" height="26" viewBox="0 0 14 26"><path d="M2 1l10 12L2 25" stroke="#777" fill="none"/></svg>
<div class="abs products">
  <div class="card"><div class="shot" role="img" aria-label="White Qavrixes 7 smartphone, front view"></div><h4>Qavrixes 7</h4><div class="price">Get up to ₱18,500 <svg width="10" height="10" viewBox="0 0 10 10"><circle cx="5" cy="5" r="5" fill="var(--blue)"/><path d="M4 2.8L6.2 5 4 7.2" stroke="#fff" stroke-width="1.5" fill="none"/></svg></div></div>
  <div class="card"><div class="shot" role="img" aria-label="White Turnwell Orbit S6 smartphone, front view"></div><h4>Turnwell Orbit S6</h4><div class="price">Get up to ₱12,800 <svg width="10" height="10" viewBox="0 0 10 10"><circle cx="5" cy="5" r="5" fill="var(--blue)"/><path d="M4 2.8L6.2 5 4 7.2" stroke="#fff" stroke-width="1.5" fill="none"/></svg></div></div>
  <div class="card"><div class="shot dark" role="img" aria-label="Black Qavrixes 6 smartphone showing the lock screen"></div><h4>Qavrixes 6</h4><div class="price">Get up to ₱13,200 <svg width="10" height="10" viewBox="0 0 10 10"><circle cx="5" cy="5" r="5" fill="var(--blue)"/><path d="M4 2.8L6.2 5 4 7.2" stroke="#fff" stroke-width="1.5" fill="none"/></svg></div></div>
  <div class="card"><div class="shot gold" role="img" aria-label="Champagne Turnwell Orbit S5 smartphone showing the home screen"></div><h4>Turnwell Orbit S5</h4><div class="price">Get up to ₱9,400 <svg width="10" height="10" viewBox="0 0 10 10"><circle cx="5" cy="5" r="5" fill="var(--blue)"/><path d="M4 2.8L6.2 5 4 7.2" stroke="#fff" stroke-width="1.5" fill="none"/></svg></div></div>
</div>

<section class="abs cta">
  <h2>BUY AND SELL SMARTPHONES</h2>
  <p>We are a privately held firm dedicated to clients who have entrusted</p>
  <div class="btn">CLICK HERE</div>
</section>

<footer class="footer">
  <div class="abs brand">TORVADEX</div>
  <h5 class="abs col-title" style="left:237px">Contact us</h5>
  <div class="abs col-text" style="left:237px;top:1075px">Address : 12 Halden St, Riverside<br>Pasig, 1600 PH<br>Phone : 632-555-0172.<br>Email : info@torvadexmail.com</div>
  <h5 class="abs col-title" style="left:429px">Sign up for newsletter</h5>
  <div class="abs col-text" style="left:429px;top:1073px;width:135px;line-height:10.5px">Your about us information would fit here nicely.</div>
  <div class="abs newsletter"><div class="field">Email address</div><div class="submit">Submit</div></div>
  <h5 class="abs col-title" style="left:626px">Follow us out there</h5>
  <div class="abs follow"><i></i><i></i><i></i><i></i></div>
  <div class="abs rule"></div>
  <div class="abs copyright">Copyright © 2017. All Rights Reserved</div>
</footer>

</body>
</html>
```